Marlowe Group needs a business card

I would like the card to be simple but modern and elegant.
I like black and white.
or black and gold.
we are a private finance lender and also are involved in property and property developments.

please look at the business card photos i provided i would like M.G only one one side and all the other details on the other side use fonts that tie in with my theme.

Industry/Entity Type

Finance

Contact Information for Business Card

Marlowe Group (M.G) Daniel Marlowe M: 0413586207 E: danmarl@inboxmail.test

Font styles to use
Other font styles liked:
• Use fonts that would reflect our business

Colors
000000
ffffff

Requirements
Must have
• one side of details
• other side has either M.G or Marlowe Group like in the photos provided

```html
<!DOCTYPE html>
<html lang="en">
<head>
<meta charset="utf-8">
<title>Marlowe Group – Business Card</title>
<link rel="stylesheet" href="https://fonts.googleapis.com/css2?family=Cinzel:wght@500;600&family=Open+Sans:wght@400&display=swap">
<style>
  :root {
    --page-bg: #e9e7e4;
    --card-black: #000000;
    --gold: #f2c230;
    --gold-light: #ffe27a;
    --gold-deep: #c9961c;
    --silver: #cfc6c0;
    --text-white: #ffffff;
  }
  * { margin: 0; padding: 0; box-sizing: border-box; }
  html, body {
    width: 1200px;
    height: 900px;
    overflow: hidden;
    background: var(--page-bg);
  }
  .card {
    position: absolute;
    left: 110px;
    top: 146px;
    width: 980px;
    height: 607px;
    background: var(--card-black);
  }
  .brand-square {
    position: absolute;
    left: 57px;
    top: 96px;
    width: 413px;
    height: 413px;
    padding: 15px;
    background: linear-gradient(135deg, var(--silver), #8f837c 50%, var(--silver));
  }
  .brand-square-inner {
    width: 100%;
    height: 100%;
    border: 16px solid var(--gold);
    background: var(--card-black);
    display: flex;
    align-items: center;
    justify-content: center;
  }
  .brand-name {
    font-family: "Cinzel", serif;
    font-weight: 500;
    font-size: 34px;
    color: var(--gold);
    letter-spacing: 0.5px;
  }
  .holder-name {
    position: absolute;
    left: 517px;
    top: 184px;
    font-family: "Cinzel", serif;
    font-weight: 600;
    font-size: 44px;
    color: var(--gold);
    white-space: nowrap;
  }
  .contact-list {
    position: absolute;
    left: 522px;
    top: 332px;
    list-style: none;
    font-family: "Open Sans", sans-serif;
    font-size: 31px;
    color: var(--text-white);
  }
  .contact-item {
    display: flex;
    align-items: center;
    height: 41px;
  }
  .contact-icon {
    width: 22px;
    margin-right: 12px;
    flex: none;
  }
</style>
</head>
<body>
  <section class="card" aria-label="Marlowe Group business card">
    <div class="brand-square">
      <div class="brand-square-inner">
        <span class="brand-name">Marlowe Group</span>
      </div>
    </div>

    <h1 class="holder-name">Daniel Marlowe</h1>

    <ul class="contact-list">
      <li class="contact-item">
        <svg class="contact-icon" viewBox="0 0 22 30" aria-hidden="true">
          <rect x="3" y="2" width="16" height="26" rx="3" fill="none" stroke="var(--gold)" stroke-width="3"/>
          <circle cx="11" cy="23" r="1.8" fill="var(--gold)"/>
        </svg>
        <span>0413586207</span>
      </li>
      <li class="contact-item">
        <svg class="contact-icon" viewBox="0 0 22 16" aria-hidden="true">
          <rect x="0" y="0" width="22" height="16" fill="var(--gold)"/>
          <polyline points="1,1 11,9 21,1" fill="none" stroke="var(--card-black)" stroke-width="1.8"/>
        </svg>
        <span>danmarl@inboxmail.test</span>
      </li>
    </ul>
  </section>
</body>
</html>
```